Corvane Card

The logo is the Spanish flag colors I want a vibrant eye catching design with the yellow / red colors over either Navy or white background or black even ,
Would like a 2D feel to the logo with another lighter color logo under it look ,

Contact Information for Business Card

Corvane Flooring
Teodor Vashkin
Main Number
Cell Number
Fax Number

Website on the side of the card somewhere

Font styles to use
Sans Serif

Colors
ec1f27
ffc214

Requirements
Must have
• 2 logos feel one is bolder and the other one underneath very light

```html
<!DOCTYPE html>
<html lang="en">
<head>
<meta charset="utf-8">
<title>Corvane Flooring – Business Card</title>
<link rel="stylesheet" href="https://fonts.googleapis.com/css2?family=Montserrat:wght@300;400;600;800&display=swap">
<style>
  :root {
    --brand-red: #ec1f27;
    --brand-yellow: #ffc214;
    --card-black: #0a0a0a;
    --divider: #3a3a3a;
    --text-light: #e6e6e6;
    --backdrop: #c9c9c9;
  }
  * { box-sizing: border-box; margin: 0; padding: 0; }
  html, body {
    width: 1200px; height: 900px; overflow: hidden;
    background: var(--backdrop);
    font-family: "Montserrat", sans-serif;
  }
  .stage { position: relative; width: 1200px; height: 900px; }

  .card {
    position: absolute;
    width: 560px; height: 320px;
    background: var(--card-black);
    border-radius: 26px;
    overflow: hidden;
  }
  .card--front { left: 80px; top: 90px; }
  .card--back  { left: 560px; top: 490px; }

  .wordmark {
    display: flex; align-items: center; gap: 12px;
    font-weight: 800; color: var(--brand-red);
    text-transform: uppercase; letter-spacing: 2px; line-height: 1.05;
  }
  .wordmark__square {
    width: 26px; height: 26px; background: var(--brand-yellow); border-radius: 4px; flex: none;
  }
  .card--front .wordmark {
    position: absolute; left: 0; right: 0; top: 110px;
    justify-content: center; font-size: 38px;
  }
  .card--back .wordmark {
    position: absolute; left: 36px; top: 120px; font-size: 26px;
  }
  .card--back .wordmark__square { width: 20px; height: 20px; }

  .divider {
    position: absolute; left: 262px; top: 62px;
    width: 1px; height: 150px; background: var(--divider);
  }

  .contact { position: absolute; left: 288px; top: 62px; }
  .contact__name {
    font-weight: 800; font-size: 20px; letter-spacing: 1px;
    text-transform: uppercase; margin-bottom: 12px;
  }
  .contact__first { color: var(--brand-red); }
  .contact__last { color: var(--brand-yellow); }
  .contact__list { list-style: none; }
  .contact__item {
    display: flex; align-items: center; gap: 10px;
    font-weight: 300; font-size: 15px; color: var(--text-light);
    margin-bottom: 7px;
  }
  .contact__icon { width: 18px; height: 18px; flex: none; }

  .web-band {
    position: absolute; left: 0; right: 0; bottom: 0; height: 66px;
    background: var(--brand-red);
    border-top: 4px solid var(--brand-yellow);
    display: flex; align-items: center; justify-content: center;
    color: var(--brand-yellow);
    font-weight: 600; font-size: 14px; letter-spacing: 4px; text-transform: uppercase;
  }
</style>
</head>
<body>
<main class="stage">

  <section class="card card--front" aria-label="Business card front">
    <div class="wordmark">
      <span class="wordmark__square"></span>
      <span>Corvane<br>Flooring</span>
    </div>
  </section>

  <section class="card card--back" aria-label="Business card back">
    <div class="wordmark">
      <span class="wordmark__square"></span>
      <span>Corvane<br>Flooring</span>
    </div>

    <div class="divider"></div>

    <div class="contact">
      <p class="contact__name"><span class="contact__first">Teodor</span> <span class="contact__last">Vashkin</span></p>
      <ul class="contact__list">
        <li class="contact__item">
          <svg class="contact__icon" viewBox="0 0 18 18" aria-hidden="true">
            <rect x="1" y="1" width="16" height="16" rx="3" fill="none" stroke="#ec1f27" stroke-width="1.6"/>
            <path d="M6 4.5l2 2-1 1.2c.6 1.3 1.6 2.3 2.9 2.9l1.2-1 2 2-1.3 1.4C8.9 12.6 5.4 9.1 4.6 5.8z" fill="#ec1f27"/>
          </svg>
          044 7310 2264
        </li>
        <li class="contact__item">
          <svg class="contact__icon" viewBox="0 0 18 18" aria-hidden="true">
            <rect x="5" y="1.5" width="8" height="4" fill="#ec1f27"/>
            <rect x="1.5" y="6" width="15" height="7" rx="1.5" fill="#ec1f27"/>
            <rect x="5" y="11" width="8" height="5.5" fill="#0a0a0a" stroke="#ec1f27" stroke-width="1.4"/>
          </svg>
          044 7310 2265
        </li>
        <li class="contact__item">
          <svg class="contact__icon" viewBox="0 0 18 18" aria-hidden="true">
            <rect x="1" y="4" width="16" height="11" fill="#ec1f27"/>
            <path d="M1 4l8 6 8-6" fill="none" stroke="#0a0a0a" stroke-width="1.4"/>
          </svg>
          info@corvaneflooring.com
        </li>
      </ul>
    </div>

    <div class="web-band">www.corvaneflooring.com</div>
  </section>

</main>
</body>
</html>
```